Brightlane Rapid Rinse Web Design

We are looking for a web design that highlights our state of the art fully automated commercial vehicle washing equipment. Similar system to a car wash however this system is meant for the largest vehicles on our roadways. Transport trucks with or without a trailer, busses both highway and school, RV's from 5th wheel type to A Class. Cement trucks, dump trucks, vac trucks, fuel trucks etc. Pick ups with utility trailers...Refrigerator truck clean outs.
Brightlane Rapid Rinse will wash your vehicle quickly and with a minimal impact on the environment

Home page
About us
Why Brightlane
Services and pricing
Videos of wash system
Fleets
contact us

Target Market(s)

Commercial vehicle owners and operators as well as corporate fleets. Includes busses, municipal, school and highway.both school and

Industry/Entity Type

transportation

Coding

Coded - Design and coding required

Number of Pages Required

5+ page

Font styles to use
Sans Serif

Colors
0054AA
0677BA
7BADD7
CADEEF
E8F1F8

Requirements
Must have
• Welcome page,why us page which describes the financial and environmental benefits. payment processing page, contact us page, Services which is washing vehicles and greasing for commercial vehicles that want that service and grease
Nice to have
• pictures of both clean and dirty commercial vehicles ie. before and after

```html
<!DOCTYPE html>
<html lang="en">
<head>
<meta charset="utf-8">
<title>Brightlane Rapid Rinse</title>
<link href="https://fonts.googleapis.com/css2?family=Montserrat:wght@600;700;800&family=Roboto:ital,wght@0,400;0,500;0,700;1,400&display=swap" rel="stylesheet">
<style>
:root{
  --blue-deep:#0054AA;
  --blue:#0677BA;
  --blue-soft:#7BADD7;
  --blue-pale:#CADEEF;
  --blue-mist:#E8F1F8;
  --ink:#111;
  --text:#555;
  --white:#fff;
}
*{margin:0;padding:0;box-sizing:border-box}
html,body{width:1200px;height:4141px;overflow:hidden}
body{position:relative;background:var(--white);font-family:"Roboto",sans-serif;color:var(--ink)}
.abs{position:absolute}
.heading{font-family:"Montserrat",sans-serif;font-weight:700;text-transform:uppercase;color:var(--ink)}
.section-title{position:absolute;left:0;width:1200px;text-align:center;font-size:40px}
.section-title::after{content:"";display:block;width:62px;height:4px;background:var(--blue-deep);margin:14px auto 0}
.btn{position:absolute;display:flex;align-items:center;justify-content:center;gap:6px;height:48px;border-radius:24px;background:var(--blue-deep);color:var(--white);font-weight:700;font-size:14px;text-transform:uppercase}
.btn .dot{width:13px;height:13px;border-radius:50%;background:var(--white);display:inline-flex;align-items:center;justify-content:center}
.photo{position:absolute}

/* header */
.site-header{position:absolute;left:0;top:0;width:1200px;height:92px;background:#000}
.brand{position:absolute;left:111px;top:26px;color:var(--white);font-family:"Montserrat",sans-serif;font-weight:700;font-size:17px;line-height:1}
.brand small{display:block;margin-top:6px;font-size:11px;letter-spacing:4px;color:var(--blue)}
.nav{position:absolute;left:326px;top:0;display:flex;height:92px;gap:29px}
.nav a{color:var(--white);font-size:14px;line-height:92px;text-decoration:none;position:relative}
.nav a.active::before{content:"";position:absolute;left:0;right:0;top:22px;height:2px;background:var(--blue)}
.call{position:absolute;left:915px;top:0;width:285px;height:92px;background:var(--blue-deep);clip-path:polygon(36px 0,100% 0,100% 100%,0 100%)}
.call .icon{position:absolute;left:50px;top:29px;width:34px;height:34px;border-radius:50%;background:var(--white);display:flex;align-items:center;justify-content:center}
.call p{position:absolute;left:98px;top:26px;color:var(--white);font-size:14px}
.call strong{position:absolute;left:98px;top:42px;color:var(--white);font-size:21px;font-weight:700}

/* hero */
.hero{position:absolute;left:0;top:92px;width:1200px;height:629px;background:linear-gradient(100deg,#2b3340 0%,#4a5666 35%,#6e6a5e 60%,#3a4656 100%)}
.hero-title{position:absolute;left:111px;top:154px;color:var(--white);font-size:53px;line-height:60px;font-family:"Montserrat",sans-serif;font-weight:700}
.hero-tag{position:absolute;left:117px;top:280px;padding:2px 10px;background:var(--white);border:3px solid var(--blue);color:var(--blue);font-family:"Montserrat",sans-serif;font-weight:700;font-size:37px;line-height:42px}
.hero-text{position:absolute;left:111px;top:343px;width:560px;color:var(--white);font-size:14px;line-height:21px}
.btn.light{background:var(--white);color:var(--ink)}
.slider-arrow{position:absolute;width:42px;height:42px;border-radius:50%;background:var(--white);display:flex;align-items:center;justify-content:center}

/* about */
.badge{position:absolute;left:174px;top:868px;width:118px;height:118px;border-radius:50%;background:var(--blue-deep);border:4px solid var(--white);color:var(--white);text-align:center;padding-top:22px;font-size:14px;line-height:16px}
.badge b{display:block;font-size:27px;line-height:30px}
.about-box{position:absolute;left:620px;top:911px;width:480px;height:380px;background:var(--white)}
.about-box p{position:absolute;left:28px;width:440px;font-size:14px;line-height:26px;color:var(--text);text-align:justify}

/* services */
.ring{position:absolute;top:1466px;width:438px;height:438px;border-radius:50%;background:var(--white);border:19px solid var(--blue-soft);text-align:center}
.ring.featured{border-color:var(--blue-deep);z-index:2}
.ring .svc-icon{position:absolute;left:157px;top:55px;width:86px;height:86px;border-radius:50%;background:var(--blue-deep);display:flex;align-items:center;justify-content:center}
.ring h3{position:absolute;left:0;right:0;top:173px;font-size:20px;font-weight:700;text-transform:uppercase;font-family:"Roboto",sans-serif}
.ring p{position:absolute;left:40px;right:40px;top:213px;font-size:14px;line-height:26px;color:var(--text)}
.ring .btn{left:119px;top:312px;width:162px}

/* testimonial */
.band{position:absolute;left:0;top:2570px;width:1200px;height:321px;background:var(--blue-deep)}
.quote-card{position:absolute;left:111px;top:2669px;width:488px;height:264px;background:var(--white)}
.quote-card h2{position:absolute;left:30px;top:36px;font-size:29px}
.quote-card blockquote{position:absolute;left:35px;top:104px;width:432px;font-size:14px;line-height:26px;font-style:italic;color:var(--text);text-align:justify}
.quote-card .name{position:absolute;left:37px;top:218px;font-size:19px;font-weight:500;color:#333}
.quote-card .role{position:absolute;left:37px;top:246px;font-size:13px;color:#555}

/* faq */
.faq-item{position:absolute;left:257px;width:683px;height:58px;border-radius:29px;background:var(--white);box-shadow:0 3px 10px rgba(0,0,0,.1);display:flex;align-items:center;padding-left:40px;font-size:14px;color:#555}
.faq-item .plus{position:absolute;right:12px;top:11px;width:36px;height:36px;border-radius:50%;background:var(--blue-deep);color:var(--white);font-size:16px;display:flex;align-items:center;justify-content:center}

/* footer */
.site-footer{position:absolute;left:0;top:3713px;width:1200px;height:428px;background:linear-gradient(160deg,#0a5fc0,#0054AA 50%,#0a4fa0)}
.f-brand{position:absolute;left:145px;top:110px;color:var(--white);font-family:"Montserrat",sans-serif;font-weight:700;font-size:27px;line-height:1}
.f-brand small{display:block;font-size:18px;letter-spacing:6px;margin-top:6px}
.social{position:absolute;top:179px;width:32px;height:32px;border-radius:50%;border:2px solid var(--white)}
.f-col{position:absolute;top:100px;color:var(--white)}
.f-col h4{font-size:16px;font-weight:700;text-transform:uppercase;margin-bottom:18px}
.f-col li{list-style:none;font-size:13px;line-height:27px}
.contact-row{position:relative;padding-left:36px;font-size:13px;line-height:18px;margin-bottom:13px}
.contact-row b{display:block;font-size:11px}
.contact-row svg{position:absolute;left:10px;top:2px}
.copyright{position:absolute;left:0;width:1200px;top:363px;text-align:center;color:var(--white);font-size:14px}
.to-top{position:absolute;left:1112px;top:312px;width:34px;height:34px;border-radius:50%;background:var(--blue);display:flex;align-items:center;justify-content:center}
</style>
</head>
<body>

<header class="site-header">
  <div class="brand">BRIGHTLANE<small>RAPID RINSE</small></div>
  <nav class="nav">
    <a class="active" href="#">Home</a><a href="#">About Us</a><a href="#">Why Brightlane</a><a href="#">Services and pricing</a><a href="#">Contact</a><a href="#">More</a>
  </nav>
  <div class="call">
    <span class="icon"><svg width="18" height="18" viewBox="0 0 24 24"><path fill="#0054AA" d="M6.6 10.8a15 15 0 0 0 6.6 6.6l2.2-2.2a1 1 0 0 1 1-.25 11.4 11.4 0 0 0 3.6.57 1 1 0 0 1 1 1V20a1 1 0 0 1-1 1A17 17 0 0 1 3 4a1 1 0 0 1 1-1h3.5a1 1 0 0 1 1 1c0 1.25.2 2.45.57 3.57a1 1 0 0 1-.25 1z"/></svg></span>
    <p>Call Us Today :</p>
    <strong>+1 555 010 2040</strong>
  </div>
</header>

<section class="hero" role="img" aria-label="Row of transport trucks parked at a wash bay at dusk">
  <h1 class="hero-title">BRIGHTLANE<br>RAPID RINSE</h1>
  <div class="hero-tag">(LESS THAN 15 MINUTES)</div>
  <p class="hero-text">A concise statement about our dedication to revolutionizing truck washing with advanced technology and sustainable practices, set against a dark blue backdrop.</p>
  <a class="btn" style="left:111px;top:402px;width:164px">Book a Wash</a>
  <a class="btn light" style="left:282px;top:402px;width:164px">Learn More</a>
  <a class="btn" style="left:453px;top:402px;width:164px">Contact Us</a>
  <span class="slider-arrow" style="left:991px;top:541px"><svg width="12" height="12" viewBox="0 0 12 12"><path d="M8 1 3 6l5 5" stroke="#111" stroke-width="1.8" fill="none"/></svg></span>
  <span class="slider-arrow" style="left:1044px;top:541px"><svg width="12" height="12" viewBox="0 0 12 12"><path d="m4 1 5 5-5 5" stroke="#111" stroke-width="1.8" fill="none"/></svg></span>
</section>

<section class="about">
  <div class="photo" role="img" aria-label="Worker pressure washing a truck inside a wash bay" style="left:234px;top:830px;width:529px;height:375px;background:linear-gradient(120deg,#6d7378,#b9bec2 55%,#e4e6e8)"></div>
  <div class="photo" role="img" aria-label="Worker spraying an orange utility truck outdoors" style="left:112px;top:1019px;width:326px;height:267px;background:#fff;padding:4px"><div style="width:100%;height:100%;background:linear-gradient(160deg,#8fb6e0,#c9d6df 45%,#d77a3a 70%,#7c8a6a)"></div></div>
  <div class="badge"><b>25</b>Years<br>Experience</div>
  <div class="about-box">
    <h2 class="heading" style="position:absolute;left:28px;top:24px;font-size:38px">About Us</h2>
    <span class="abs" style="left:28px;top:82px;width:64px;height:4px;background:var(--blue-deep)"></span>
    <p style="top:100px">Lorem ipsum dolor sit amet, consectetur adipiscing elit, sed do eiusmod tempor incididunt ut labore et dolore magna aliqua. Ut enim ad minim veniam, quis nostrud exercitation ullamco laboris nisi ut aliquip ex ea commodo consequat.</p>
    <p style="top:228px">Duis aute irure dolor in reprehenderit in voluptate velit esse cillum dolore eu fugiat nulla pariatur.Lorem ipsum dolor sit amet, consec tetur adipiscing elit, sed do eiusmod tempor incididunt</p>
    <a class="btn" style="left:28px;top:324px;width:164px">Learn More <span class="dot"><svg width="7" height="7" viewBox="0 0 8 8"><path d="m2 1 3 3-3 3" stroke="#0054AA" stroke-width="1.6" fill="none"/></svg></span></a>
  </div>
</section>

<section class="services">
  <h2 class="heading section-title" style="top:1376px">Our Services</h2>
  <div class="ring" style="left:-20px">
    <span class="svc-icon"><svg width="46" height="34" viewBox="0 0 46 34" fill="none" stroke="#fff" stroke-width="2"><rect x="2" y="6" width="26" height="18"/><path d="M28 12h9l6 7v5H28z"/><circle cx="11" cy="27" r="4"/><circle cx="36" cy="27" r="4"/></svg></span>
    <h3>Automated Truck Wash</h3>
    <p>Lorem ipsum dolor sit amet, consectetur adipi scing elit, sed do eiusmod tempor incididunt ut labore et dolore magna aliqua.</p>
    <a class="btn">Learn More <span class="dot"><svg width="7" height="7" viewBox="0 0 8 8"><path d="m2 1 3 3-3 3" stroke="#0054AA" stroke-width="1.6" fill="none"/></svg></span></a>
  </div>
  <div class="ring featured" style="left:381px">
    <span class="svc-icon"><svg width="46" height="34" viewBox="0 0 46 34" fill="none" stroke="#fff" stroke-width="2"><path d="M4 4l14 10M2 22h30v-8h8l4 6v2"/><circle cx="10" cy="27" r="4"/><circle cx="34" cy="27" r="4"/></svg></span>
    <h3>Additional Services</h3>
    <p>Lorem ipsum dolor sit amet, consectetur adipi scing elit, sed do eiusmod tempor incididunt ut labore et dolore magna aliqua.</p>
    <a class="btn">Learn More <span class="dot"><svg width="7" height="7" viewBox="0 0 8 8"><path d="m2 1 3 3-3 3" stroke="#0054AA" stroke-width="1.6" fill="none"/></svg></span></a>
  </div>
  <div class="ring" style="left:782px">
    <span class="svc-icon"><svg width="40" height="40" viewBox="0 0 40 40" fill="none" stroke="#fff" stroke-width="2"><rect x="6" y="4" width="20" height="14" rx="2"/><rect x="14" y="20" width="20" height="14" rx="2"/><circle cx="11" cy="21" r="2"/><circle cx="29" cy="36" r="2"/></svg></span>
    <h3>Fleet Services</h3>
    <p>Lorem ipsum dolor sit amet, consectetur adipi scing elit, sed do eiusmod tempor incididunt ut labore et dolore magna aliqua.</p>
    <a class="btn">Learn More <span class="dot"><svg width="7" height="7" viewBox="0 0 8 8"><path d="m2 1 3 3-3 3" stroke="#0054AA" stroke-width="1.6" fill="none"/></svg></span></a>
  </div>
</section>

<section class="projects">
  <h2 class="heading section-title" style="top:1996px">Our Projects</h2>
  <div class="photo" role="img" aria-label="Dirty truck wheel being washed, before cleaning" style="left:111px;top:2088px;width:241px;height:305px;background:linear-gradient(160deg,#d8d8d8,#6a6a6a 60%,#3a3a3a)"></div>
  <div class="photo" role="img" aria-label="Clean semi truck at sunset" style="left:352px;top:2088px;width:241px;height:305px;background:linear-gradient(180deg,#f2c38a,#c77e4e 45%,#2f4a5e 80%,#4a4a4a)"></div>
  <div class="photo" role="img" aria-label="Fuel tanker wheels being pressure washed" style="left:606px;top:2088px;width:241px;height:305px;background:linear-gradient(150deg,#e4b680,#8a6040 50%,#3a3430)"></div>
  <div class="photo" role="img" aria-label="Clean white truck with trailer on the highway" style="left:847px;top:2088px;width:241px;height:305px;background:linear-gradient(180deg,#3f7fc4,#a8c9e6 45%,#d8dde0 65%,#6a6e70)"></div>
  <svg class="abs" style="left:45px;top:2231px" width="14" height="24" viewBox="0 0 14 24"><path d="M12 2 2 12l10 10" stroke="#111" stroke-width="2.2" fill="none"/></svg>
  <svg class="abs" style="left:1136px;top:2231px" width="14" height="24" viewBox="0 0 14 24"><path d="m2 2 10 10L2 22" stroke="#111" stroke-width="2.2" fill="none"/></svg>
</section>

<section class="testimonials">
  <div class="band"></div>
  <div class="photo" role="img" aria-label="Worker washing a blue truck at night" style="left:519px;top:2517px;width:567px;height:416px;background:linear-gradient(120deg,#1d3f7a,#3a63b8 35%,#7d8590 60%,#22262c)"></div>
  <div class="quote-card">
    <h2 class="heading">What Our Clients Say</h2>
    <span class="abs" style="left:30px;top:82px;width:64px;height:4px;background:var(--blue-deep)"></span>
    <blockquote>"Lorem ipsum dolor sit amet, consectetur adipiscing elit, sed do eiusmod tempor incididunt ut labore et dolore magna aliqua. Ut enim ad minim veniam, quis nostrud exercitation ullamco laboris nisi ut aliquip ex ea commodo consequat. "</blockquote>
    <div class="name">Dana Whitfield</div>
    <div class="role">Company name</div>
    <svg class="abs" style="left:364px;top:236px" width="32" height="18" viewBox="0 0 32 18"><path d="M30 9H3M10 2 3 9l7 7" stroke="#aaa" stroke-width="2" fill="none"/></svg>
    <svg class="abs" style="left:406px;top:236px" width="32" height="18" viewBox="0 0 32 18"><path d="M2 9h27M22 2l7 7-7 7" stroke="#0054AA" stroke-width="2.4" fill="none"/></svg>
  </div>
</section>

<section class="faq">
  <h2 class="heading section-title" style="top:3066px">Frequently Asked Questions</h2>
  <div class="faq-item" style="top:3181px">Lorem ipsum dolor sit amet, consectetur adipiscing elit, sed<span class="plus">+</span></div>
  <div class="faq-item" style="top:3250px">Lorem ipsum dolor sit amet, consectetur adipiscing elit, sed<span class="plus">+</span></div>
  <div class="faq-item" style="top:3319px">Lorem ipsum dolor sit amet, consectetur adipiscing elit, sed<span class="plus">+</span></div>
  <div class="faq-item" style="top:3387px">Lorem ipsum dolor sit amet, consectetur adipiscing elit, sed<span class="plus">+</span></div>
  <div class="faq-item" style="top:3456px">Lorem ipsum dolor sit amet, consectetur adipiscing elit, sed<span class="plus">+</span></div>
  <a class="btn" style="left:518px;top:3530px;width:164px">View More <span class="dot"><svg width="7" height="7" viewBox="0 0 8 8"><path d="m2 1 3 3-3 3" stroke="#0054AA" stroke-width="1.6" fill="none"/></svg></span></a>
</section>

<footer class="site-footer">
  <div class="f-brand">BRIGHTLANE<small>RAPID RINSE</small></div>
  <span class="social" style="left:193px"></span>
  <span class="social" style="left:234px"></span>
  <span class="social" style="left:275px"></span>
  <div class="f-col" style="left:432px">
    <h4>Quick Links</h4>
    <ul><li>Home</li><li>About us</li><li>Our Services</li><li>News</li><li>Contact Us</li></ul>
  </div>
  <div class="f-col" style="left:613px">
    <h4>About Company</h4>
    <ul><li>Legal Information</li><li>Terms &amp; Condition</li><li>Privacy Policy</li><li>Support</li><li>Site Map</li></ul>
  </div>
  <div class="f-col" style="left:843px;width:300px">
    <h4>Contact Us</h4>
    <div class="contact-row"><svg width="12" height="12" viewBox="0 0 24 24"><path fill="#fff" d="M6.6 10.8a15 15 0 0 0 6.6 6.6l2.2-2.2a1 1 0 0 1 1-.25 11.4 11.4 0 0 0 3.6.57 1 1 0 0 1 1 1V20a1 1 0 0 1-1 1A17 17 0 0 1 3 4a1 1 0 0 1 1-1h3.5a1 1 0 0 1 1 1c0 1.25.2 2.45.57 3.57a1 1 0 0 1-.25 1z"/></svg><b>Phone</b>+1 (555) 010-2040</div>
    <div class="contact-row"><svg width="14" height="11" viewBox="0 0 14 11"><rect width="14" height="11" fill="#fff"/><path d="m0 0 7 6 7-6" stroke="#0054AA" fill="none"/></svg><b>Email</b>hello@brightlanerinse.example</div>
    <div class="contact-row"><svg width="11" height="15" viewBox="0 0 12 16"><path fill="#fff" d="M6 0a6 6 0 0 0-6 6c0 4.5 6 10 6 10s6-5.5 6-10a6 6 0 0 0-6-6zm0 8.5A2.5 2.5 0 1 1 6 3.5a2.5 2.5 0 0 1 0 5z"/></svg><b>Location</b>123, Lorem ipsum dolor sit amet,<br>consectetur adipiscing</div>
  </div>
  <span class="to-top"><svg width="12" height="8" viewBox="0 0 12 8"><path d="m1 7 5-5 5 5" stroke="#fff" stroke-width="2" fill="none"/></svg></span>
  <p class="copyright">2024 Copyrights Company name &nbsp;| All Rights Reserved</p>
</footer>

</body>
</html>
```